Sole Relationship Graphic of Chapter Organization for Book

This design shows relationships between variables associated with footwear and footprints. It will be used as a graphic in a book. The four elements of the graphic are (1) Variables, (2) Book Chapter Numbers (which correspond to the relationship(s) between at least two variables, (3) Relationship Arrows, and (4) Influence Arrows (because the influencers affect the variables differently than relationships between the variables). These names simply relate to the attempts I have made (and attached) at creating a graphic. In the attached diagrams, the circles with numbers are placeholders for the book chapter numbers, which may be changed so it will be good if I can change those after the graphic is completed. Chapter 1 will be the introduction.
The intent of of outsourcing this project is not necessarily sticking to the formats I have attached, but to allow your creativity to produce a useful graphic that can visually make the most sense of the relationships between the variables as chapters to readers of the book.

Target Market(s)

Search and Rescue Trackers

Requirements
Must have
• Information listed in project description, and drafted in attached diagrams
Nice to have
• Can include outlines of barefoot and outsoles. While Chapters 1 (Intro), 2 (Missing Persons' Footwear), 10 (Case Studies) and 11 (Summary) are set, the others aren't. The end game of this book is to use the rest of the variables to arrive at the end game, which is measurements for barefoot track length or outsole track length...so those two variables can be highlighted in some way to emphasize their importance.

```html
<!DOCTYPE html>
<html lang="en">
<head>
<meta charset="utf-8">
<title>Sole Relationship Graphic – Chapter Organization</title>
<link href="https://fonts.googleapis.com/css2?family=Roboto+Condensed:wght@500;700&display=swap" rel="stylesheet">
<style>
  :root {
    --green: #218b6e;
    --dark: #4b5350;
    --paper: #ffffff;
    --shoe-grey: #d6d6d6;
    --foot-red: #b71f2b;
  }
  html, body {
    margin: 0;
    padding: 0;
    width: 1200px;
    height: 675px;
    overflow: hidden;
    background: var(--paper);
  }
  .diagram {
    display: block;
    width: 1200px;
    height: 675px;
    font-family: "Roboto Condensed", "Arial Narrow", sans-serif;
  }
  .node-frame { fill: var(--paper); stroke: var(--green); stroke-width: 3; }
  .node-band { fill: var(--green); }
  .node-label { fill: #fff; font-size: 19px; font-weight: 700; text-anchor: middle; }
  .shoe-art { fill: var(--shoe-grey); }
  .foot-art { fill: var(--foot-red); }
  .influencer-box { fill: var(--dark); }
  .influencer-label { fill: #fff; font-size: 21px; font-weight: 700; text-anchor: middle; }
  .size-box { fill: var(--green); }
  .size-label { fill: #fff; font-size: 19px; font-weight: 700; text-anchor: middle; }
  .relation { fill: none; stroke: var(--dark); stroke-width: 3.5; }
  .influence { fill: none; stroke: var(--green); stroke-width: 3.5; }
  .chapter-ring { fill: #fff; stroke: var(--green); stroke-width: 2.5; }
  .chapter-num { fill: var(--green); font-size: 17px; font-weight: 700; text-anchor: middle; dominant-baseline: central; }
  .track-disc { fill: var(--dark); }
  .track-label { fill: var(--dark); font-size: 19px; font-weight: 700; text-anchor: middle; }
  .input-label { fill: var(--dark); font-size: 19px; font-weight: 700; text-anchor: middle; }
  .legend-title { fill: var(--dark); font-size: 18px; font-weight: 700; }
  .legend-frame { fill: none; stroke: var(--dark); stroke-width: 2; }
  .legend-text { fill: var(--dark); font-size: 15px; font-weight: 500; }
  .legend .chapter-num { font-size: 14px; }
</style>
</head>
<body>
<svg class="diagram" viewBox="0 0 1280 720" xmlns="http://www.w3.org/2000/svg" aria-labelledby="diagram-title">
  <title id="diagram-title">Relationships between footwear and footprint variables, by book chapter</title>
  <defs>
    <marker id="head-dark" viewBox="0 0 10 10" refX="8" refY="5" markerWidth="4" markerHeight="4" orient="auto-start-reverse">
      <path d="M0 0 L10 5 L0 10 Z" fill="var(--dark)"/>
    </marker>
    <marker id="head-green" viewBox="0 0 10 10" refX="8" refY="5" markerWidth="4" markerHeight="4" orient="auto-start-reverse">
      <path d="M0 0 L10 5 L0 10 Z" fill="var(--green)"/>
    </marker>
  </defs>

  <!-- Connectors -->
  <g class="connectors">
    <line class="influence" x1="193" y1="172" x2="311" y2="172" marker-end="url(#head-green)"/>
    <line class="relation" x1="477" y1="172" x2="815" y2="172" marker-start="url(#head-dark)" marker-end="url(#head-dark)"/>
    <line class="relation" x1="978" y1="172" x2="1088" y2="172" marker-end="url(#head-dark)"/>
    <path class="influence" d="M573 287 H443 V244" marker-end="url(#head-green)"/>
    <path class="influence" d="M718 283 H897 V244" marker-end="url(#head-green)"/>
    <line class="influence" x1="646" y1="323" x2="646" y2="392" marker-end="url(#head-green)"/>
    <path class="influence" d="M558 416 H400 V244" marker-end="url(#head-green)"/>
    <line class="influence" x1="646" y1="435" x2="646" y2="495" marker-end="url(#head-green)"/>
    <path class="influence" d="M352 244 V546 H564" marker-start="url(#head-green)" marker-end="url(#head-green)"/>
    <line class="influence" x1="483" y1="595" x2="564" y2="595" marker-end="url(#head-green)"/>
    <line class="relation" x1="723" y1="564" x2="884" y2="564" marker-end="url(#head-dark)"/>
  </g>

  <!-- Variables -->
  <g class="node node-insole">
    <rect class="node-frame" x="315" y="88" width="156" height="150"/>
    <rect class="shoe-art" x="328" y="100" width="132" height="82" rx="8" role="img" aria-label="Shoe outline with the insole traced in red"/>
    <rect class="node-band" x="315" y="202" width="156" height="36"/>
    <text class="node-label" x="393" y="227">Insole</text>
  </g>

  <g class="node node-outsole">
    <rect class="node-frame" x="821" y="88" width="156" height="150"/>
    <rect class="shoe-art" x="834" y="100" width="132" height="82" rx="8" role="img" aria-label="Shoe outline with the outsole traced in red"/>
    <rect class="node-band" x="821" y="202" width="156" height="36"/>
    <text class="node-label" x="899" y="227">Outsole</text>
  </g>

  <g class="node node-barefoot">
    <rect class="node-frame" x="570" y="501" width="152" height="126"/>
    <rect class="foot-art" x="596" y="513" width="100" height="66" rx="8" role="img" aria-label="Side view of a bare foot in red"/>
    <rect class="node-band" x="570" y="590" width="152" height="37"/>
    <text class="node-label" x="646" y="615">Barefoot</text>
  </g>

  <g class="influencer">
    <rect class="influencer-box" x="573" y="244" width="145" height="79" rx="12"/>
    <text class="influencer-label" x="645.5" y="279">Individual</text>
    <text class="influencer-label" x="645.5" y="302">Variation</text>
  </g>

  <g class="nominal-size">
    <rect class="size-box" x="558" y="398" width="175" height="37"/>
    <text class="size-label" x="645.5" y="423">Nominal Size</text>
  </g>

  <text class="input-label" x="160" y="166">Hook</text>
  <text class="input-label" x="160" y="187">Area</text>
  <text class="input-label" x="448" y="602">Height</text>

  <!-- Track outcomes -->
  <g class="track track-shod">
    <circle class="track-disc" cx="1133" cy="172" r="43" role="img" aria-label="Shod footprint track icon"/>
    <text class="track-label" x="1135" y="238">Shod Track</text>
  </g>
  <g class="track track-barefoot">
    <circle class="track-disc" cx="933" cy="560" r="43" role="img" aria-label="Barefoot footprint track icon"/>
    <text class="track-label" x="932" y="626">Barefoot Track</text>
  </g>

  <!-- Chapter markers -->
  <g class="chapters">
    <g><circle class="chapter-ring" cx="246" cy="145" r="13"/><text class="chapter-num" x="246" y="145">3</text></g>
    <g><circle class="chapter-ring" cx="646" cy="145" r="13"/><text class="chapter-num" x="646" y="145">8</text></g>
    <g><circle class="chapter-ring" cx="1033" cy="145" r="13"/><text class="chapter-num" x="1033" y="145">9</text></g>
    <g><circle class="chapter-ring" cx="531" cy="313" r="13"/><text class="chapter-num" x="531" y="313">10</text></g>
    <g><circle class="chapter-ring" cx="757" cy="313" r="13"/><text class="chapter-num" x="757" y="313">10</text></g>
    <g><circle class="chapter-ring" cx="673" cy="353" r="13"/><text class="chapter-num" x="673" y="353">10</text></g>
    <g><circle class="chapter-ring" cx="324" cy="388" r="13"/><text class="chapter-num" x="324" y="388">5</text></g>
    <g><circle class="chapter-ring" cx="475" cy="456" r="13"/><text class="chapter-num" x="475" y="456">4</text></g>
    <g><circle class="chapter-ring" cx="673" cy="466" r="13"/><text class="chapter-num" x="673" y="466">4</text></g>
    <g><circle class="chapter-ring" cx="800" cy="537" r="13"/><text class="chapter-num" x="800" y="537">7</text></g>
    <g><circle class="chapter-ring" cx="521" cy="616" r="13"/><text class="chapter-num" x="521" y="616">8</text></g>
  </g>

  <!-- Legend -->
  <g class="legend">
    <text class="legend-title" x="67" y="532">LEGEND</text>
    <rect class="legend-frame" x="65" y="546" width="223" height="89"/>
    <circle class="chapter-ring" cx="142" cy="567" r="10"/>
    <text class="chapter-num" x="142" y="567">1</text>
    <text class="legend-text" x="170" y="572">Chapter #</text>
    <line class="relation" x1="72" y1="593" x2="151" y2="593" stroke-width="3" marker-end="url(#head-dark)"/>
    <text class="legend-text" x="170" y="598">Relationship to</text>
    <line class="influence" x1="72" y1="618" x2="151" y2="618" stroke-width="3" marker-end="url(#head-green)"/>
    <text class="legend-text" x="170" y="623">Influence on</text>
  </g>
</svg>
</body>
</html>
```